Website Design for a holiday home letting busines

We require a redesign of our present website www.pinebrookstays.com. We want the website to stand out and look professional and clean to make holiday hunters want to book a caravan or lodge holiday with us. Our logo is red however we DO NOT want the website to be red. We want a natural colour scheme.

The final design should communicate that we are a professional company to book with.

On the home page we require;
Overview of company
Photo
Search box for holiday (check in)
Late Deals
Reviews
News

We would like the following pages designed; home page, available dates page, caravans page, content page.

The website should be responsive for smart phones. One website I do like is http://www.verdoliso.be/nl/

Target Market(s)

Families

Industry/Entity Type

Travel

Number of Pages Required

5+ page

Font styles to use
Serif

Requirements
Must have
• The project must be responsive for mobile phones and tablets.
• Ability to search for holiday home holidays
• We want a natural colour scheme.
Nice to have
• A style we like is http://www.verdoliso.be/nl/
Should not have
• Do not use red as a colour for the website. Our logo is red so this is the only time we want this used.

```html
<!DOCTYPE html>
<html lang="en">
<head>
<meta charset="utf-8">
<title>Pinebrook Stays – Private Holiday Rentals</title>
<link rel="stylesheet" href="https://fonts.googleapis.com/css2?family=Oswald:wght@400;500;600&family=Open+Sans:wght@400;600;700&display=swap">
<style>
:root{
  --teal:#1ba89a;
  --teal-dark:#13897d;
  --orange:#f6b259;
  --orange-deep:#f29a34;
  --cta:#d9342b;
  --ink:#333a40;
  --muted:#6b7278;
  --white:#ffffff;
  --line:#dcdcdc;
  --hero-sky:#9cc3d8;
  --hero-rock:#d99a5e;
}
*{box-sizing:border-box;margin:0;padding:0}
html,body{width:1200px;height:2532px;overflow:hidden}
body{position:relative;background:var(--white);font-family:"Open Sans",Arial,sans-serif;color:var(--ink)}
.abs{position:absolute}
h1,h2,h3,h4{font-family:"Oswald","Arial Narrow",sans-serif;font-weight:500;letter-spacing:.5px}

/* hero */
.hero{left:0;top:0;width:1200px;height:660px;background:linear-gradient(180deg,var(--hero-sky) 0%,#c9b9a0 40%,var(--hero-rock) 75%,#c47f45 100%)}
.topnav{left:118px;top:0;width:964px;height:42px;background:var(--white);display:flex;align-items:center;justify-content:center;font-size:11.5px;white-space:nowrap;overflow:hidden}
.topnav a{color:var(--ink);text-decoration:none;padding:0 9px;line-height:42px;height:42px;border-right:1px solid var(--line);white-space:nowrap;flex:none}
.topnav a:last-child{border-right:none}
.topnav a.current{background:var(--teal);color:var(--white)}
.brand{left:440px;top:62px;width:320px;height:58px;background:var(--white);border-radius:6px;display:flex;align-items:center;justify-content:center;gap:12px}
.brand .mark{width:28px;height:28px;border-radius:50%;background:var(--cta)}
.brand span{font-family:"Oswald",sans-serif;font-size:26px;font-weight:500;color:var(--cta)}
.hero-title{left:120px;top:236px;font-size:46px;color:var(--white);font-weight:600;white-space:nowrap}
.hero-copy{left:120px;top:306px;width:460px;font-size:16px;line-height:26px;color:var(--white)}
.btn-teal{background:var(--teal);color:var(--white);font-size:18px;font-weight:600;border-radius:4px;display:flex;align-items:center;justify-content:center}
.more{left:120px;top:430px;width:140px;height:46px}
.villa{left:750px;top:190px;width:340px;height:340px;border-radius:50%;border:8px solid var(--white);background:radial-gradient(circle at 45% 40%,#f2c98a 0%,#c58a52 45%,#5fa0c9 80%,#2b78b1 100%)}

/* booking */
.booking{left:120px;top:660px;width:960px;height:118px;background:var(--white);display:flex}
.booking .label{width:270px;background:var(--teal);color:var(--white);padding:22px 22px}
.booking .label h3{font-size:28px;font-weight:500}
.booking .label small{font-size:11px;line-height:15px;display:block;margin-top:4px}
.booking form{flex:1;display:flex;align-items:flex-end;gap:12px;padding:0 18px 32px}
.field{display:flex;flex-direction:column;font-size:10px;color:var(--muted);white-space:nowrap}
.field .box{margin-top:5px;height:30px;border:1px solid var(--line);font-size:11px;color:var(--ink);display:flex;align-items:center;padding:0 8px}
.book{height:40px;width:100px;background:var(--cta);color:var(--white);font-weight:700;font-size:15px;display:flex;align-items:center;justify-content:center;border-radius:3px;margin-left:auto}

/* intro */
.intro{left:0;top:778px;width:1200px;height:392px;background:var(--orange)}
.video{left:120px;top:810px;width:400px;height:240px;background:linear-gradient(135deg,#2c4a6e,#5d86b5);border:6px solid var(--white)}
.play{left:300px;top:910px;width:50px;height:40px}
.intro-title{left:560px;top:810px;font-size:34px;color:var(--ink);white-space:nowrap}
.intro-copy{left:560px;top:862px;width:520px;font-size:12.5px;line-height:20px;color:var(--ink)}
.intro-copy p{margin-bottom:14px}

/* sections */
.section-title{left:0;width:1200px;text-align:center;font-size:38px;color:var(--teal-dark)}
.rule{left:520px;width:160px;height:3px;background:var(--orange-deep)}
.card{width:280px;height:210px;border:6px solid var(--white);box-shadow:0 2px 6px rgba(0,0,0,.2)}
.card.feature{padding:30px 24px;color:var(--white)}
.card.feature h3{font-size:24px;font-weight:500;margin-bottom:8px}
.card.feature li{list-style:none;font-size:12px;line-height:20px;padding-left:70px}
.photo-room{background:linear-gradient(160deg,#f1f0ec,#b9b6ad 60%,#6f6a62)}
.photo-pool{background:linear-gradient(180deg,#d9e9f3 0%,#ede6da 45%,#4fb6d6 75%,#2a8fbd 100%)}
.photo-villa{background:linear-gradient(180deg,#8fc0e0 0%,#f1ead9 55%,#d1b58d 100%)}

/* reviews */
.reviews{left:0;top:1830px;width:1200px;height:418px;background:var(--teal)}
.reviews-title{left:120px;top:1880px;width:720px;text-align:center;font-size:34px;color:var(--white)}
.avatar{left:440px;top:1950px;width:90px;height:90px;border-radius:50%;background:linear-gradient(180deg,#cfd8dc,#7d8b93);border:4px solid var(--white)}
.quote{left:200px;top:2064px;width:570px;text-align:center;font-size:12.5px;line-height:20px;color:var(--white)}
.check{left:425px;top:2140px;width:120px;height:32px;background:var(--teal-dark);color:var(--white);font-size:12px;font-weight:600;border-radius:3px;display:flex;align-items:center;justify-content:center;border:1px solid rgba(255,255,255,.5)}
.news{left:888px;top:1850px;width:200px;height:390px;background:var(--white);padding:12px 14px}
.news h3{font-size:18px;color:var(--ink);border-bottom:2px solid var(--orange-deep);padding-bottom:4px;margin-bottom:10px}
.news h3 b{color:var(--teal);font-weight:500}
.news article{font-size:10.5px;line-height:15px;color:var(--muted);padding:10px 0;border-bottom:1px solid var(--line)}

/* footer */
.footer{left:0;top:2248px;width:1200px;height:284px;background:var(--white)}
.fcol{top:2278px;font-size:12px;line-height:21px}
.fcol h4{font-size:16px;margin-bottom:4px;color:var(--ink)}
.fcol li{list-style:none;color:var(--muted)}
.fcol li::before{content:"› ";color:var(--teal)}
.badge{left:948px;top:2272px;width:100px;height:100px;border-radius:50%;background:var(--teal);border:5px solid #a7dcd5}
.social{top:2396px;width:26px;height:26px;border-radius:50%;background:var(--teal)}
.card-pay{top:2440px;width:38px;height:24px;border-radius:3px;background:#d8dde0}
.legal{left:120px;top:2470px;width:620px;font-size:10px;line-height:15px;color:var(--muted)}
</style>
</head>
<body>

<header class="abs hero">
  <nav class="abs topnav">
    <a class="current">Home</a><a>News</a><a>Reviews</a><a>Caravans &amp; Lodges</a><a>2015 Holidays</a><a>2016 Holidays</a><a>Payment Plans</a><a>Kestrel Bay Guide</a><a>Local Attractions</a><a>Contact Us</a>
  </nav>
  <div class="abs brand"><i class="mark"></i><span>Pinebrook Stays</span></div>
  <h1 class="abs hero-title">PRIVATE HOLIDAY RENTALS</h1>
  <p class="abs hero-copy">Relax in a welcoming caravan or lodge close to the sea, with room for the whole family and everything you need for a calm break away.</p>
  <div class="abs btn-teal more">Know More</div>
  <div class="abs villa" role="img" aria-label="Photo of a holiday villa with a swimming pool"></div>
</header>

<section class="abs booking">
  <div class="label">
    <h3>Online Booking</h3>
    <small>Pick your dates and find a holiday home that suits you.</small>
  </div>
  <form>
    <label class="field" style="width:130px">Type of caravan<span class="box">Any ▾</span></label>
    <label class="field" style="width:120px">Check in date<span class="box">26/08/2015</span></label>
    <label class="field" style="width:120px">Check out date<span class="box">28/08/2015</span></label>
    <label class="field" style="width:54px">Adults<span class="box">2 ▾</span></label>
    <label class="field" style="width:54px">Children<span class="box">0 ▾</span></label>
    <span class="book">Book now</span>
  </form>
</section>

<section class="abs intro"></section>
<div class="abs video" role="img" aria-label="Video preview of a family holiday at the park"></div>
<svg class="abs play" viewBox="0 0 50 40"><rect width="50" height="40" rx="8" fill="#ffffff" opacity=".9"/><path d="M20 12 L33 20 L20 28Z" fill="#1ba89a"/></svg>
<h2 class="abs intro-title">NO DEPOSIT HOLIDAYS</h2>
<div class="abs intro-copy">
  <p>Would you like to book a 2016 caravan or lodge holiday at Kestrel Bay with no deposit at all?</p>
  <p>We have flexible low cost weekly and monthly payment plans available online so you can spread the cost of your stay. This means you can secure your holiday now without making one large payment and still enjoy the same great rates.</p>
  <p>Once you add to the direct debit mandate, payments start within 21 days. You even get the chance to choose what day of the week or month the payments are taken from your bank. If you prefer to make a full deposit or secure the date, the balance is due before your holiday.</p>
  <p>If you have any questions about our hassle free direct debit payment plans please contact us and we will be more than happy to help.</p>
</div>

<h2 class="abs section-title" style="top:1222px">OUR CARAVANS &amp; LODGES</h2>
<div class="abs rule" style="top:1276px"></div>
<div class="abs card feature" style="left:120px;top:1298px;background:var(--teal)">
  <h3>Heatherdale</h3>
  <ul><li>Spacious Lodge</li><li>Sleeps Six</li><li>Two Bedrooms</li><li>Sea View Deck</li></ul>
</div>
<div class="abs card photo-room" style="left:460px;top:1298px" role="img" aria-label="Photo of a bright lodge living room"></div>
<div class="abs card photo-pool" style="left:800px;top:1298px" role="img" aria-label="Photo of a park swimming pool"></div>

<h2 class="abs section-title" style="top:1530px">LATE DEALS</h2>
<div class="abs rule" style="top:1584px"></div>
<div class="abs card feature" style="left:120px;top:1604px;background:var(--orange-deep)">
  <h3>Heatherdale</h3>
  <ul><li>Three Nights</li><li>Sleeps Four</li><li>Pets Welcome</li><li>Late Offer</li></ul>
</div>
<div class="abs card photo-villa" style="left:460px;top:1604px" role="img" aria-label="Photo of a whitewashed holiday villa"></div>
<div class="abs card photo-pool" style="left:800px;top:1604px" role="img" aria-label="Photo of a poolside terrace"></div>

<section class="abs reviews"></section>
<h2 class="abs reviews-title">WHAT DO CUSTOMERS SAY?</h2>
<div class="abs avatar" role="img" aria-label="Customer portrait"></div>
<p class="abs quote">We had a wonderful week in our lodge. Everything was spotless and the staff were so helpful. The children loved the pool and we have already booked again for next summer with friends.</p>
<div class="abs check">Check more here</div>
<aside class="abs news">
  <h3><b>LATEST</b> NEWS</h3>
  <article>New lodges have arrived on the park for the coming season with larger decks and views.</article>
  <article>Spring opening dates are now live so you can plan your first break of the year early.</article>
  <article>The heated indoor pool has been refurbished and reopens to guests this month.</article>
  <article>Payment plans are now available on every caravan for holidays booked online.</article>
</aside>

<footer class="abs footer"></footer>
<div class="abs fcol" style="left:120px">
  <h4>Navigation</h4>
  <ul><li>About us</li><li>News</li><li>Caravans &amp; Lodges</li><li>2015 Holidays</li><li>2016 Holidays</li><li>Late Deals</li></ul>
</div>
<div class="abs fcol" style="left:380px">
  <h4>More Link</h4>
  <ul><li>Kestrel Bay Guide</li><li>Local Attractions</li><li>Special Offers</li><li>Contact Us</li><li>Reviews</li><li>Guest Stories</li></ul>
</div>
<div class="abs fcol" style="left:640px">
  <h4>More link</h4>
  <ul><li>Frequently Asked Questions</li><li>Terms &amp; Conditions</li><li>Privacy Policy</li><li>Booking Terms</li></ul>
</div>
<div class="abs badge" role="img" aria-label="Rating badge"></div>
<i class="abs social" style="left:960px"></i><i class="abs social" style="left:994px"></i><i class="abs social" style="left:1028px"></i>
<i class="abs card-pay" style="left:936px"></i><i class="abs card-pay" style="left:980px"></i><i class="abs card-pay" style="left:1024px"></i>
<p class="abs legal">Pinebrook Stays is an independent letting company offering privately owned caravans and lodges at Kestrel Bay. All holidays are subject to availability and our booking terms. www.pinebrookstays.com</p>

</body>
</html>
```